Bry7Legal Letterhead

Need a new letterhead for my law firm.
IDENTIFYING INFORMATION BELOW:
Anselmo R Quintara III
Attorney at Law
Address: 2847 Larkspur Blvd, Ste 300, Dallas, TX 75204
Phone: 877-482-6017
Fax: 469-738-1452
Email: bry@bry7legal.example
Website: www.bry7legal.example

Colors
0054AA
0677BA
7BADD7
CADEEF
E8F1F8

Requirements
Must have
• Logo needs to be on the letterhead, along with identifying information which is included in the project description.

```html
<!DOCTYPE html>
<html lang="en">
<head>
<meta charset="utf-8">
<title>Bry7Legal Letterhead</title>
<link rel="stylesheet" href="https://fonts.googleapis.com/css2?family=Arimo:wght@400;700&family=Roboto:wght@400;500&display=swap">
<style>
  :root {
    --backdrop: #adabac;
    --paper-light: #ffffff;
    --paper-dark: #d6d6d7;
    --ink: #111111;
    --body-ink: #4a4a4a;
    --accent: #0b93d1;
    --accent-deep: #0054aa;
    --rule: #7badd7;
    --band: #222222;
  }
  * { margin: 0; padding: 0; box-sizing: border-box; }
  html, body { width: 1039px; height: 1200px; overflow: hidden; }
  body { background: var(--backdrop); position: relative; font-family: "Arimo", sans-serif; }

  .letterhead {
    position: absolute; left: 159px; top: 98px; width: 710px; height: 1001px;
    background: linear-gradient(160deg, var(--paper-light) 0%, #eeeeee 45%, var(--paper-dark) 100%);
    overflow: hidden;
  }

  .brand-name {
    position: absolute; left: 53px; top: 56px;
    font-family: "Arimo", sans-serif; font-weight: 700; font-size: 25px;
    letter-spacing: 1px; color: var(--ink); text-transform: uppercase;
  }

  .attorney {
    position: absolute; right: 184px; top: 57px; text-align: right;
    font-family: "Roboto", sans-serif;
  }
  .attorney-name { font-size: 15.5px; font-weight: 500; color: var(--accent); line-height: 19px; }
  .attorney-title { font-size: 10px; color: var(--ink); line-height: 13px; }

  .contact-divider {
    position: absolute; left: 539px; top: 61px; width: 1px; height: 94px; background: var(--rule);
  }

  .contact {
    position: absolute; left: 551px; top: 57px;
    font-family: "Roboto", sans-serif; font-size: 10.5px; color: var(--ink); line-height: 13px;
  }
  .contact-address { margin-bottom: 6px; }
  .contact-list { list-style: none; }
  .contact-list li { display: flex; align-items: center; gap: 4px; height: 13px; }
  .contact-list svg { width: 9px; height: 9px; flex: none; }

  .letter-body {
    position: absolute; left: 53px; top: 334px; width: 600px; color: var(--body-ink);
  }
  .salutation { font-size: 15px; line-height: 22px; margin-bottom: 14px; }
  .letter-body p { font-size: 11.2px; line-height: 16.8px; text-align: justify; margin-bottom: 17px; }
  .closing { margin-top: 0; }

  .signature {
    position: absolute; left: 53px; top: 679px; width: 90px; height: 36px;
    background: linear-gradient(90deg, rgba(40,48,60,0.15), rgba(40,48,60,0.3), rgba(40,48,60,0.1));
    border-radius: 3px;
  }

  .footer-band { position: absolute; left: 0; bottom: 0; width: 100%; height: 7px; background: var(--band); }
  .footer-accent {
    position: absolute; left: 532px; bottom: 0; width: 89px; height: 7px;
    background: linear-gradient(90deg, var(--accent-deep), var(--accent), var(--accent-deep));
    border-left: 1px solid #e8f1f8; border-right: 1px solid #e8f1f8;
  }
</style>
</head>
<body>
  <main class="letterhead">
    <div class="brand-name">Bry7Legal</div>

    <div class="attorney">
      <div class="attorney-name">Anselmo R Quintara III</div>
      <div class="attorney-title">Attorney at Law</div>
    </div>

    <div class="contact-divider"></div>

    <div class="contact">
      <div class="contact-address">2847 Larkspur Blvd<br>Ste 300<br>Dallas, TX 75204</div>
      <ul class="contact-list">
        <li>
          <svg viewBox="0 0 10 10" aria-hidden="true"><path d="M2 0.8 L3.6 2.8 L2.8 3.8 Q4 6 6.2 7.2 L7.2 6.4 L9.2 8 L8 9.4 Q3.8 9 0.6 2 Z" fill="var(--accent)"/></svg>
          877-482-6017
        </li>
        <li>
          <svg viewBox="0 0 10 10" aria-hidden="true"><rect x="2.5" y="0.5" width="5" height="3" fill="none" stroke="var(--accent)"/><rect x="0.5" y="3.5" width="9" height="4" fill="var(--accent)"/><rect x="2.5" y="6.5" width="5" height="3" fill="#fff" stroke="var(--accent)"/></svg>
          469-738-1452
        </li>
        <li>
          <svg viewBox="0 0 10 10" aria-hidden="true"><rect x="0.5" y="2" width="9" height="6.5" fill="var(--accent)"/><path d="M0.8 2.4 L5 6 L9.2 2.4" fill="none" stroke="#fff" stroke-width="0.9"/></svg>
          bry@bry7legal.example
        </li>
        <li>
          <svg viewBox="0 0 10 10" aria-hidden="true"><g fill="none" stroke="var(--accent)" stroke-width="0.8"><circle cx="5" cy="5" r="4.3"/><ellipse cx="5" cy="5" rx="2" ry="4.3"/><path d="M0.7 5 H9.3 M1.5 2.8 H8.5 M1.5 7.2 H8.5"/></g></svg>
          www.bry7legal.example
        </li>
      </ul>
    </div>

    <section class="letter-body">
      <div class="salutation">Dear Mr. Harlow,</div>
      <p>Lorem ipsum dolor sit amet, consectetur adipiscing elit. Donec orci purus, luctus vitae dignissim eu, iaculis sed purus. Vivamus faucibus, ipsum nec aliquet viverra, leo mauris condimentum ligula, sit amet sagittis enim ligula quis arcu. Nam egestas tortor id nisi porttitor mattis. In tortor ante, ultricies in suscipit a, tempus non massa. Vivamus et auctor mi. Fusce vel massa nulla. Phasellus nec eros mauris, et scelerisque orci.</p>
      <p>Donec malesuada orci vitae nulla accumsan porta a id massa. Quisque accumsan iaculis magna sit amet fringilla. Maecenas consequat, magna eget tincidunt semper, odio nibh rutrum mi, id feugiat ante nisi eu risus. Vestibulum nunc orci, rhoncus a placerat in, ultricies in mi. Cras mattis varius eros, vel fringilla nisi suscipit eget. Quisque scelerisque sagittis nulla at porttitor.</p>
      <p>Sed id augue vitae urna euismod commodo aliquet a quam. Pellentesque arcu velit, cursus et malesuada ut, consequat et diam. Nullam erat sem, rhoncus id ullamcorper vitae, rhoncus et arcu. In ultricies ultricies nulla, ut rutrum nisi iaculis at. Donec eu magna a metus ornare faucibus. Fusce aliquet faucibus ultricies. Morbi semper, est id tincidunt gravida, sem arcu adipiscing lacus, ac bibendum nulla leo eu purus. Quisque nec diam sed risus consectetur accumsan quis quis nibh. Vestibulum id purus lorem.</p>
      <p class="closing">Sincerely,</p>
    </section>

    <div class="signature" role="img" aria-label="Handwritten signature of the attorney"></div>

    <div class="footer-band"></div>
    <div class="footer-accent"></div>
  </main>
</body>
</html>
```